W. Darrow Billboard

2 miles ahead on right
Voted number 1 ... again!
California cuisine
Located in Historic Marbury Hill Inn
Picture of a couple dining
www.torvellis.com 555.317.2968

Target Market(s)

travelers

Industry/Entity Type

hospitality

Font styles to use
Serif

Colors
59FF00
82FF00
B8FF75
E3FFCB
F4FFEA
EE7325
F08F49
F5BC92
FAE3D3
FDF4ED

Requirements
Should not have
• bright colors

```html
<!DOCTYPE html>
<html lang="en">
<head>
<meta charset="utf-8">
<title>Torvelli's Southwest Bar &amp; Grill Billboard</title>
<link href="https://fonts.googleapis.com/css2?family=Roboto+Slab:wght@800&family=Poppins:wght@600&family=Barlow+Condensed:wght@600;700&family=Oswald:wght@600;700&display=swap" rel="stylesheet">
<style>
  :root {
    --page: #dedede;
    --paper: #ffffff;
    --brand-orange: #ea4c26;
    --lime: #bfd730;
    --ink: #141414;
    --night: #0d0d0d;
    --photo-dark: #2a1d15;
    --photo-warm: #7a5233;
  }
  * { margin: 0; padding: 0; box-sizing: border-box; }
  html, body { width: 1192px; height: 1200px; overflow: hidden; background: var(--page); }
  .billboard {
    position: absolute; left: 46px; top: 440px;
    width: 1100px; height: 319px;
    background: var(--paper);
    box-shadow: 0 14px 28px rgba(0,0,0,.28);
    overflow: hidden;
  }
  .billboard__art { position: absolute; inset: 0; }
  .brand {
    position: absolute; left: 30px; top: 70px; width: 370px;
    text-align: center; color: var(--brand-orange);
    font-family: "Roboto Slab", serif; font-weight: 800;
  }
  .brand__name { font-size: 74px; line-height: 1; letter-spacing: -1px; }
  .brand__tagline { font-size: 21px; letter-spacing: 3px; margin-top: 6px; }
  .brand__sub { font-size: 15px; letter-spacing: 2px; margin-top: 2px; }
  .website {
    position: absolute; left: 40px; top: 262px; width: 340px; text-align: center;
    font-family: "Poppins", sans-serif; font-weight: 600; font-size: 28px; color: var(--ink);
  }
  .cuisine {
    position: absolute; left: 400px; top: 248px; width: 390px; text-align: center;
    font-family: "Barlow Condensed", sans-serif; line-height: 1.05;
  }
  .cuisine__title { color: var(--lime); font-weight: 700; font-size: 28px; letter-spacing: .5px; }
  .cuisine__location { color: #fff; font-weight: 600; font-size: 21px; }
  .award {
    position: absolute; left: 880px; top: 22px; width: 195px;
    font-family: "Oswald", sans-serif; font-weight: 700; color: #fff; line-height: 1;
    text-shadow: 1px 2px 3px rgba(0,0,0,.35);
  }
  .award__voted { font-size: 44px; }
  .award__rank { font-size: 108px; letter-spacing: -3px; margin-top: -4px; }
  .award__again { font-size: 38px; text-align: right; margin-top: -4px; }
  .phone {
    position: absolute; left: 810px; top: 252px; width: 290px; text-align: center;
    font-family: "Oswald", sans-serif; font-weight: 600; font-size: 50px; line-height: 1;
    color: var(--ink); letter-spacing: -1px;
  }
</style>
</head>
<body>
  <main class="billboard">
    <svg class="billboard__art" width="1100" height="319" viewBox="0 0 1100 319">
      <defs>
        <linearGradient id="photoTone" x1="0" y1="0" x2="1" y2="1">
          <stop offset="0" stop-color="var(--photo-dark)"/>
          <stop offset=".55" stop-color="var(--photo-warm)"/>
          <stop offset="1" stop-color="var(--photo-dark)"/>
        </linearGradient>
      </defs>
      <polygon class="photo" points="486,0 880,0 880,319 394,319" fill="url(#photoTone)" role="img" aria-label="Photo of a smiling couple toasting with red wine by candlelight"/>
      <polygon class="caption-band" points="415,245 811,245 777,319 394,319" fill="var(--night)"/>
      <polygon class="award-panel" points="869,0 1100,0 1100,245 811,245" fill="var(--brand-orange)"/>
      <polygon class="phone-band" points="811,245 1100,245 1100,319 777,319" fill="var(--lime)"/>
      <polygon class="accent-stripe" points="799,245 805,245 771,319 765,319" fill="#fff"/>
      <line class="accent-line" x1="829" y1="198" x2="808" y2="245" stroke="#fff" stroke-width="3"/>
      <circle cx="831" cy="190" r="4" fill="#fff"/>
      <line class="accent-line" x1="475" y1="4" x2="452" y2="60" stroke="var(--brand-orange)" stroke-width="4"/>
      <circle cx="448" cy="74" r="4" fill="var(--brand-orange)"/>
    </svg>

    <div class="brand">
      <div class="brand__name">Torvelli's</div>
      <div class="brand__tagline">SOUTHWEST</div>
      <div class="brand__sub">BAR &amp; GRILL</div>
    </div>
    <div class="website">www.torvellis.com</div>

    <div class="cuisine">
      <div class="cuisine__title">CALIFORNIA CUISINE</div>
      <div class="cuisine__location">Located in Historic Marbury Hill Inn</div>
    </div>

    <div class="award">
      <div class="award__voted">VOTED</div>
      <div class="award__rank">NO.1</div>
      <div class="award__again">...AGAIN</div>
    </div>
    <div class="phone">555.317.2968</div>
  </main>
</body>
</html>
```